Nivel Crest - Powerpoint Templates

We are a consultancy to help builders to optimize their planning in order to save building costs. For that reason we need templates for teasers and presentations where we offer our services, show our team and their capacities and present workflows, organization charts, price lists etc.

```html
<!DOCTYPE html>
<html lang="en">
<head>
<meta charset="utf-8">
<title>Nivel Crest – Presentation Template</title>
<link href="https://fonts.googleapis.com/css2?family=Montserrat:wght@400;500;600;700;800&family=Oswald:wght@500;600&display=swap" rel="stylesheet">
<style>
:root{
  --gold:#d4a23c;
  --gold-dark:#b9852a;
  --ink:#2f2f33;
  --text:#7b7b7e;
  --line:#9a9a9d;
  --stage:#8e8e91;
  --panel:#3b3b3f;
  --white:#ffffff;
}
*{margin:0;padding:0;box-sizing:border-box}
html,body{width:1200px;height:1153px;overflow:hidden}
body{background:var(--stage);font-family:"Montserrat",sans-serif;color:var(--ink);position:relative}
.slide{position:absolute;width:374px;height:210px;background:var(--white);overflow:hidden;box-shadow:0 2px 5px rgba(0,0,0,.35)}
.c1{left:28px}.c2{left:412px}.c3{left:798px}
.r1{top:28px}.r2{top:250px}.r3{top:470px}.r4{top:694px}.r5{top:915px}
.abs{position:absolute}
.gold{color:var(--gold)}
.body{position:absolute;font-size:4.2px;line-height:1.4;color:var(--text)}
.just{text-align:justify}
.brand-mini{position:absolute;right:14px;top:10px;display:flex;align-items:center;gap:2px;font-size:5px;font-weight:700;color:var(--gold);letter-spacing:.3px}
.brand-mini i{display:block;width:5px;height:5px;background:var(--gold)}
.folio{position:absolute;left:14px;bottom:8px;font-size:6px;font-weight:600;color:var(--ink)}
.folio-line{position:absolute;left:26px;right:30px;bottom:11px;height:.6px;background:var(--line)}
.photo{position:absolute}
.h-light{font-weight:500;text-transform:uppercase}
.h-bold{font-weight:800;text-transform:uppercase;color:var(--gold)}
.bullet{position:absolute;font-size:4.2px;line-height:1.4;color:var(--text);padding-left:13px}
.bullet::before{content:"";position:absolute;left:0;top:1px;border-left:5px solid var(--gold);border-top:3px solid transparent;border-bottom:3px solid transparent}
.bullet.hollow::before{border-left-color:transparent}
.bullet.hollow::after{content:"▷";position:absolute;left:0;top:-1px;color:var(--gold);font-size:6px}

.cover-photo{inset:0;background:linear-gradient(170deg,#5a4a3e 0%,#8a6a4a 25%,#3a3c52 55%,#1b1e33 100%)}
.cover-brand{left:15px;top:58px;color:var(--gold);font-weight:800;font-size:11px;letter-spacing:1px}
.cover-tag{left:24px;top:72px;color:var(--gold);font-size:4.5px;font-weight:700;letter-spacing:1.2px}
.cover-kicker{left:15px;top:117px;color:#fff;font-size:10px;font-weight:500}
.cover-title{left:14px;top:127px;color:var(--gold);font-size:29px;font-weight:800;line-height:1}
.cover-sub{left:15px;top:158px;color:#fff;font-size:21px;font-weight:700;line-height:1}
.cover-rule{left:15px;top:184px;width:124px;height:1.5px;background:#fff}
.cover-url{left:15px;top:190px;color:#fff;font-size:7.5px;letter-spacing:1.6px}

.contents-title{left:26px;top:24px;font-size:19px;font-weight:800;letter-spacing:.5px}
.contents-rule{left:26px;top:47px;width:84px;height:2.5px;background:var(--gold)}
.toc{position:absolute;width:150px}
.toc b{position:absolute;left:-15px;top:0;font-size:9px;font-weight:700}
.toc h4{font-size:8.5px;font-weight:600;color:var(--gold)}
.toc p{font-size:4.5px;line-height:1.35;color:var(--text);margin-top:2px}

.about-panel{left:0;top:22px;width:198px;height:158px;background:linear-gradient(90deg,var(--panel),#56565a)}
.ico-ring{position:absolute;width:29px;height:29px;border-radius:50%;background:linear-gradient(135deg,#f0c766,var(--gold-dark));display:flex;align-items:center;justify-content:center}
.ico-ring span{width:21px;height:21px;border-radius:50%;border:1.5px solid #fff;display:flex;align-items:center;justify-content:center}
.feat{position:absolute;left:222px;width:135px}
.feat h4{font-size:8px;font-weight:600}
.feat p{font-size:4.2px;line-height:1.4;color:var(--text);margin-top:2px}

.team-band{left:0;top:88px;width:374px;height:87px;background:var(--gold)}
.member{position:absolute;top:96px;width:80px;text-align:center}
.avatar{width:31px;height:31px;border-radius:50%;margin:0 auto;background:linear-gradient(#d9d9d9,#a8a8a8);border:2px solid #fff;box-shadow:0 0 0 1px #666}
.member h5{font-size:6.8px;font-weight:700;color:var(--ink);margin-top:3px}
.member p{font-size:3.3px;line-height:1.35;color:#fff;margin-top:1px}

.price{position:absolute;top:36px;width:72px;height:152px}
.price .card{position:absolute;left:2px;top:10px;width:68px;height:132px;border-radius:12px 12px 18px 18px;box-shadow:0 2px 4px rgba(0,0,0,.35)}
.price .tab{position:absolute;left:6px;top:8px;width:60px;height:17px;border-radius:6px;color:#fff;font-size:7px;font-weight:600;text-align:center;line-height:17px}
.price .strip{position:absolute;left:2px;top:31px;width:68px;height:6px;background:#2a2a2d;color:#fff;font-size:2.8px;line-height:6px;text-align:center}
.price ul{position:absolute;left:10px;top:42px;list-style:none;font-size:3.8px;color:#fff}
.price li{height:10.2px}
.price li::before{content:"✓";display:inline-block;width:4.5px;height:4.5px;border-radius:50%;background:#fff;color:#555;font-size:3px;line-height:4.5px;text-align:center;margin-right:3px}
.price .buy{position:absolute;left:9px;top:105px;width:54px;height:7px;background:#fff;color:#333;font-size:4.5px;letter-spacing:1px;text-align:center;line-height:7px;font-weight:500}
.price .badge{position:absolute;left:0;top:118px;width:28px;height:28px;border-radius:50%;background:#fff;border:2.5px solid #888;font-size:10px;font-weight:500;text-align:center;line-height:24px;color:#333}
.price .badge sup{font-size:4px}
.price .note{position:absolute;left:30px;top:122px;width:36px;font-size:2.8px;color:#fff;text-align:center;line-height:1.3}
.price .stars{position:absolute;left:0;right:0;top:0;display:flex;justify-content:center;gap:1px}
.price .stars i{width:9px;height:9px;border-radius:50%;border:1px solid #fff;font-style:normal;font-size:5px;color:#fff;text-align:center;line-height:7px}

.phone{position:absolute;width:43px;height:91px;border:1.6px solid #222;border-radius:5px;background:#fff;padding:18px 4px 0}
.phone::before{content:"";position:absolute;left:13px;top:0;width:15px;height:2.5px;background:#222;border-radius:0 0 2px 2px}
.phone h6{font-size:5.5px;font-weight:500;line-height:1.15}
.phone .glyph{width:8px;height:6px;border:.7px solid var(--gold);margin:8px auto 6px}
.phone p{font-size:2.6px;line-height:1.35;color:var(--text);text-align:center}

.thumb{position:absolute;top:96px;width:81px;height:56px;border:1px solid #ddd}
.thumb-cap{position:absolute;top:155px;width:81px}
.thumb-cap h5{font-size:7.5px;font-weight:500;color:var(--gold)}
.thumb-cap p{font-size:3.4px;line-height:1.35;color:var(--text)}

.edu-box{position:absolute;top:47px;width:64px;height:96px;border:2.2px solid var(--ink);border-radius:8px;text-align:center;padding:14px 6px 0;background:#fff}
.edu-box h5{font-size:5.5px;font-weight:600;color:var(--gold);margin-top:3px}
.edu-box p{font-size:3.4px;line-height:1.3;color:var(--text);margin-top:5px}

.pin-label{position:absolute;width:50px}
.pin-label h6{font-size:5.5px;font-weight:500;color:var(--gold)}
.pin-label p{font-size:2.7px;line-height:1.35;color:var(--text)}
</style>
</head>
<body>

<section class="slide c1 r1">
  <div class="photo cover-photo" role="img" aria-label="Dusk city skyline with twin towers"></div>
  <div class="abs cover-brand">NIVEL CREST</div>
  <div class="abs cover-tag">BUILD SMARTER</div>
  <div class="abs cover-kicker">PRESENTATION</div>
  <div class="abs cover-title">BUSINESS</div>
  <div class="abs cover-sub">MARKETING</div>
  <div class="abs cover-rule"></div>
  <div class="abs cover-url">www.nivelcrest.com</div>
</section>

<section class="slide c2 r1">
  <div class="brand-mini"><i></i>NIVEL CREST</div>
  <h2 class="abs contents-title">CONTENTS</h2>
  <div class="abs contents-rule"></div>
  <div class="toc" style="left:56px;top:64px"><b>1.</b><h4>Lorem ipsum</h4><p>Lorem ipsum dolor sit amet, consectetuer adipiscing elit, sed diam nonummy nibh</p></div>
  <div class="toc" style="left:212px;top:64px"><b>2.</b><h4>Lorem ipsum</h4><p>Lorem ipsum dolor sit amet, consectetuer adipiscing elit, sed diam nonummy nibh euismod tincid</p></div>
  <div class="toc" style="left:56px;top:107px"><b>3.</b><h4>Lorem ipsum</h4><p>Lorem ipsum dolor sit amet, consectetuer adipiscing elit, sed diam nonummy nibh</p></div>
  <div class="toc" style="left:212px;top:107px"><b>4.</b><h4>Lorem ipsum</h4><p>Lorem ipsum dolor sit amet, consectetuer adipiscing elit, sed diam nonummy nibh euismod tincid</p></div>
  <div class="toc" style="left:56px;top:152px"><b>5.</b><h4>Lorem ipsum</h4><p>Lorem ipsum dolor sit amet, consectetuer adipiscing elit, sed diam nonummy nibh</p></div>
  <div class="toc" style="left:212px;top:152px"><b>6.</b><h4>Lorem ipsum</h4><p>Lorem ipsum dolor sit amet, consectetuer adipiscing elit, sed diam nonummy nibh euismod tincid</p></div>
  <div class="folio">02</div><div class="folio-line"></div>
</section>

<section class="slide c3 r1">
  <div class="brand-mini"><i></i>NIVEL CREST</div>
  <div class="abs about-panel"></div>
  <div class="abs gold" style="left:18px;top:28px;font-size:12px;font-weight:500">ABOUT US</div>
  <div class="abs gold" style="left:18px;top:40px;font-size:19px;font-weight:700">COMPANY</div>
  <p class="body" style="left:18px;top:70px;width:160px;color:#d5d5d8;font-size:4px">Lorem ipsum dolor sit amet, consectetuer adipiscing elit, sed diam nonummy nibh euismod tincidunt ut laoreet dolore magna aliquam erat volutpat. Ut wisi enim ad minim veniam, quis nostrud exerci tation ullamcorper suscipit lobortis nisl ut aliquip ex ea commodo consequat. Duis autem vel eum iriure dolor in hendrerit in vulputate velit esse molestie consequat, vel illum dolore eu feugiat nulla facilisis at vero eros et accumsan et iusto odio dignissim qui blandit praesent luptatum zzril delenit augue duis dolore te feugait nulla facilisi.</p>
  <p class="body" style="left:18px;top:140px;width:160px;color:#d5d5d8;font-size:4px">Lorem ipsum dolor sit amet, cons ectetuer adipiscing elit, sed diam nonummy nibh euismod tincidunt ut laoreet dolore magna aliquam erat volutpat. Ut wisi enim ad minim veniam, quis nostrud exerci tation ullamcorper suscipit lobortis nisl ut aliquip ex ea commodo consequat. Lorem ipsum dolor sit amet, consecac.</p>
  <div class="ico-ring" style="left:184px;top:35px"><span><svg width="10" height="8" viewBox="0 0 10 8"><rect x="1" y="1" width="8" height="5" fill="none" stroke="#fff" stroke-width=".8"/><path d="M3 5V3M5 5V2M7 5V4" stroke="#fff" stroke-width=".8"/></svg></span></div>
  <div class="ico-ring" style="left:184px;top:87px"><span><svg width="10" height="8" viewBox="0 0 10 8"><path d="M2 5a2 2 0 0 1 1-4 2.5 2.5 0 0 1 4.5 1A1.5 1.5 0 0 1 8 5z" fill="#fff"/><path d="M5 5v3" stroke="#fff" stroke-width=".7"/></svg></span></div>
  <div class="ico-ring" style="left:184px;top:142px"><span><svg width="10" height="8" viewBox="0 0 10 8"><path d="M1 6l3-3 2 2 3-3" fill="none" stroke="#fff" stroke-width=".9"/></svg></span></div>
  <div class="feat" style="top:35px"><h4>Lorem ipsum</h4><p>ipsum dolor sit amet, cons ectetuer adipiscing elit, sed diam nonummy nibh euismod tincidunt ut laoreet</p></div>
  <div class="feat" style="top:86px"><h4>Lorem ipsum</h4><p>ipsum dolor sit amet, cons ectetuer adipiscing elit, sed diam nonummy nibh euismod tincidunt ut laoreet dolore magna aliquam erat volutpat.</p></div>
  <div class="feat" style="top:141px"><h4>Lorem ipsum</h4><p>ipsum dolor sit amet, cons ectetuer adipiscing elit, sed diam nonummy nibh euismod tincidunt</p></div>
  <div class="folio">03</div><div class="folio-line"></div>
</section>

<section class="slide c1 r2">
  <div class="brand-mini"><i></i>NIVEL CREST</div>
  <div class="abs h-light" style="left:17px;top:17px;font-size:13px">ACTIVE</div>
  <div class="abs h-bold" style="left:17px;top:32px;font-size:13px">INTELLIGENCE</div>
  <p class="body just" style="left:17px;top:51px;width:150px">Lorem ipsum dolor sit amet, consectetuer adipiscing elit, sed diam nonummy nibh euismod tincidunt ut laoreet dolore magna aliquam erat volutpat. Ut wisi enim ad minim veniam, quis nostrud exerci tation ullamcorper suscipit lobortis nisl ut aliquip ex ea commodo consequat. Duis autem vel eum iriure dolor in hendrerit in vulputate velit esse</p>
  <p class="body just" style="left:17px;top:90px;width:150px">Lorem ipsum dolor sit amet, consectetuer adipiscing elit, sed diam nonummy nibh euismod tincidunt ut laoreet dolore magna aliquam erat volutpat. Ut wisi enim ad minim veniam, quis nostrud exerci tation ullamcorper suscipit lobortis nisl ut aliquip ex ea commodo consequat. Duis autem vel eum iriure dolor in hendrerit in vulputate velit esse</p>
  <p class="bullet" style="left:17px;top:138px;width:150px">Lorem ipsum dolor sit amet, consectetuer adipiscing elit, sed diam nonummy nibh euismod tincidunt ut laoreet dolore magna</p>
  <p class="bullet hollow" style="left:17px;top:164px;width:150px">Lorem ipsum dolor sit amet, consectetuer adipiscing elit, sed diam nonummy nibh euismod tincidunt ut laoreet dolore magna</p>
  <div class="abs" style="left:264px;top:30px;width:80px;height:2.5px;background:var(--gold)"></div>
  <div class="abs" style="left:180px;top:132px;width:2.5px;height:46px;background:var(--gold)"></div>
  <div class="abs" style="left:180px;top:176px;width:46px;height:2.5px;background:var(--gold)"></div>
  <div class="photo" style="left:185px;top:34px;width:189px;height:140px;background:linear-gradient(160deg,#8fa3b8,#4d5a6e 50%,#d9a066 85%,#2e3440)" role="img" aria-label="Glass office tower against a cloudy sunset sky"></div>
  <div class="folio">04</div><div class="folio-line"></div>
</section>

<section class="slide c2 r2">
  <div class="brand-mini"><i></i>NIVEL CREST</div>
  <div class="abs" style="left:11px;top:11px;font-size:14px;font-weight:500">OUR COMPANY <b class="gold" style="font-weight:700">EDUCATION</b></div>
  <div class="photo" style="left:52px;top:38px;width:270px;height:110px;background:radial-gradient(ellipse,#ececee 40%,transparent 72%)" role="img" aria-label="Faint world map"></div>
  <svg class="abs" style="left:0;top:0" width="374" height="210" viewBox="0 0 374 210">
    <path d="M130 124 L154 68 M216 124 L240 68" stroke="#8a8a8d" stroke-width="2.2"/>
    <circle cx="131" cy="72" r="2.5" fill="#2f2f33"/><circle cx="217" cy="72" r="2.5" fill="#2f2f33"/>
  </svg>
  <div class="edu-box" style="left:68px"><svg width="8" height="10" viewBox="0 0 8 10"><path d="M4 1a3 3 0 0 1 2 5v2H2V6a3 3 0 0 1 2-5z" fill="none" stroke="#d4a23c" stroke-width=".8"/></svg><h5>IDEA</h5><p>Lorem ipsum dolor sit amet, consectetuer adipiscing elit, sed diam nonummy nibh euismod tincidunt ut laoreet dolore magna aliquam erat volutpat. Ut wisi enim ad minim veniam</p></div>
  <div class="edu-box" style="left:154px"><svg width="10" height="10" viewBox="0 0 10 10"><rect x="1" y="2.5" width="8" height="5.5" fill="none" stroke="#d4a23c" stroke-width=".8"/><path d="M1 2.5l4 3 4-3" fill="none" stroke="#d4a23c" stroke-width=".8"/></svg><h5>PROMOTION</h5><p>Lorem ipsum dolor sit amet, consectetuer adipiscing elit, sed diam nonummy nibh euismod tincidunt ut laoreet dolore magna aliquam erat volutpat. Ut wisi enim ad minim veniam</p></div>
  <div class="edu-box" style="left:240px"><svg width="10" height="10" viewBox="0 0 10 10"><path d="M2 2v6h6M3 7l5-5M5 2h3v3" fill="none" stroke="#d4a23c" stroke-width=".8"/></svg><h5>GROWTH</h5><p>Lorem ipsum dolor sit amet, consectetuer adipiscing elit, sed diam nonummy nibh euismod tincidunt ut laoreet dolore magna aliquam erat volutpat. Ut wisi enim ad minim veniam</p></div>
  <p class="body" style="left:40px;top:157px;width:294px;text-align:center;font-size:4px">Lorem ipsum dolor sit amet, consectetuer adipiscing elit, sed diam nonummy nibh euismod tincidunt ut laoreet dolore magna aliquam erat volutpat. Ut wisi enim ad minim veniam, quis nostrud exerci tation ullamcorper suscipit lobortis nisl ut aliquip ex ea commodo consequat. Duis autem vel eum iriure dolor in hendrerit</p>
  <div class="folio">02</div><div class="folio-line"></div>
</section>

<section class="slide c3 r2">
  <div class="brand-mini"><i></i>NIVEL CREST</div>
  <div class="abs" style="left:0;top:0;width:58px;height:33px;background:linear-gradient(135deg,#f0c766,var(--gold-dark))"></div>
  <div class="photo" style="left:20px;top:36px;width:173px;height:150px;background:linear-gradient(160deg,#cfe0f0,#7f98b4 45%,#3f5068 80%,#c49a6a)" role="img" aria-label="Skyscrapers seen from street level"></div>
  <div class="abs" style="left:202px;top:34px;font-size:11px;font-weight:500;line-height:1.45">WHAT'S A DOMAIN?<br>IT'S THAT NAME UP<br><b class="gold" style="font-weight:700">IN THE ADDRESS BAR.</b></div>
  <ul class="abs" style="left:202px;top:88px;list-style:none;font-size:8.3px;color:#555;line-height:14.5px">
    <li><span class="gold">▪</span> Fits your business or products</li>
    <li><span class="gold">▪</span> Is easy to spell and remember</li>
    <li><span class="gold">▪</span> Fits your business or products</li>
    <li><span class="gold">▪</span> Is easy to spell and remember</li>
    <li><span class="gold">▪</span> Fits your business or products</li>
    <li><span class="gold">▪</span> Is easy to spell and remember</li>
    <li><span class="gold">▪</span> Fits your business or products</li>
  </ul>
  <div class="folio">06</div><div class="folio-line"></div>
</section>

<section class="slide c1 r3">
  <div class="brand-mini"><i></i>NIVEL CREST</div>
  <div class="abs h-light" style="left:17px;top:13px;font-size:13px;font-weight:600">COMPANY</div>
  <div class="abs h-bold" style="left:17px;top:27px;font-size:19px">OVERVIEW</div>
  <p class="body" style="left:17px;top:54px;width:155px">Lorem ipsum dolor sit amet, consectetuer adipiscing elit, sed diam nonummy nibh euismod tincidunt ut laoreet dolore magna aliquam erat volutpat. Ut wisi enim ad minim veniam, quis nostrud exerci tation ullamcorper suscipit lobortis nisl ut aliquip ex ea commodo consequat. Duis autem vel eum iriure dolor in hendrerit i</p>
  <p class="body" style="left:17px;top:88px;width:155px">Lorem ipsum dolor sit amet, consectetuer adipiscing elit, sed diam nonummy nibh</p>
  <svg class="abs" style="left:0;top:0" width="374" height="210" viewBox="0 0 374 210" font-family="Montserrat, sans-serif" font-size="5" fill="#555">
    <g stroke="#e2e2e2" stroke-width=".5">
      <line x1="202" y1="28" x2="356" y2="28"/><line x1="202" y1="40" x2="356" y2="40"/><line x1="202" y1="52" x2="356" y2="52"/><line x1="202" y1="64" x2="356" y2="64"/><line x1="202" y1="76" x2="356" y2="76"/><line x1="202" y1="88" x2="356" y2="88"/>
      <line x1="356" y1="28" x2="356" y2="100"/>
    </g>
    <line x1="202" y1="100" x2="356" y2="100" stroke="#999" stroke-width=".6"/>
    <line x1="202" y1="28" x2="202" y2="100" stroke="#999" stroke-width=".6"/>
    <g text-anchor="end"><text x="199" y="30">60</text><text x="199" y="42">50</text><text x="199" y="54">40</text><text x="199" y="66">30</text><text x="199" y="78">20</text><text x="199" y="90">10</text><text x="199" y="102">0</text></g>
    <rect x="216" y="52" width="4.5" height="48" fill="#d4a23c"/><rect x="224" y="40" width="4.5" height="60" fill="#3b3b3f"/>
    <rect x="252" y="86" width="4.5" height="14" fill="#3b3b3f"/><rect x="260" y="58" width="4.5" height="42" fill="#d4a23c"/>
    <rect x="285" y="31" width="4.5" height="69" fill="#3b3b3f"/><rect x="293" y="85" width="4.5" height="15" fill="#d4a23c"/>
    <rect x="319" y="38" width="4.5" height="62" fill="#d4a23c"/><rect x="327" y="65" width="4.5" height="35" fill="#3b3b3f"/>
    <g text-anchor="middle"><text x="224" y="110">JAN</text><text x="258" y="110">FEB</text><text x="291" y="110">MAR</text><text x="325" y="110">APR</text></g>
    <g stroke="#e2e2e2" stroke-width=".4">
      <line x1="24" y1="120" x2="170" y2="120"/><line x1="24" y1="129.5" x2="170" y2="129.5"/><line x1="24" y1="139" x2="170" y2="139"/><line x1="24" y1="148.5" x2="170" y2="148.5"/><line x1="24" y1="158" x2="170" y2="158"/><line x1="24" y1="167.5" x2="170" y2="167.5"/>
    </g>
    <line x1="24" y1="177" x2="170" y2="177" stroke="#999" stroke-width=".5"/>
    <g font-size="4" text-anchor="end"><text x="22" y="122">60</text><text x="22" y="131">50</text><text x="22" y="141">40</text><text x="22" y="150">30</text><text x="22" y="160">20</text><text x="22" y="169">10</text><text x="22" y="179">0</text></g>
    <g font-size="2.6" text-anchor="middle"><text x="36" y="183">TEXT 01</text><text x="52" y="183">TEXT 02</text><text x="68" y="183">TEXT 03</text><text x="84" y="183">TEXT 04</text><text x="100" y="183">TEXT 05</text><text x="116" y="183">TEXT 06</text><text x="132" y="183">TEXT 07</text><text x="148" y="183">TEXT 08</text><text x="164" y="183">TEXT 09</text></g>
    <polyline points="36,158 52,167 68,148 84,128 100,139 116,152 132,148 148,139 164,165" fill="none" stroke="#d4a23c" stroke-width=".8"/>
    <polyline points="36,177 52,167 68,153 84,162 100,139 116,149 132,156 148,146 164,137" fill="none" stroke="#2f2f33" stroke-width=".8"/>
    <g fill="#d4a23c"><circle cx="36" cy="158" r="1"/><circle cx="52" cy="167" r="1"/><circle cx="84" cy="128" r="1"/><circle cx="148" cy="139" r="1"/><circle cx="164" cy="165" r="1"/></g>
    <g fill="#2f2f33"><circle cx="36" cy="177" r="1"/><circle cx="52" cy="167" r="1"/><circle cx="84" cy="162" r="1"/><circle cx="100" cy="139" r="1"/><circle cx="132" cy="156" r="1"/><circle cx="164" cy="137" r="1"/></g>
    <circle cx="193" cy="132" r="2.5" fill="#d4a23c"/><circle cx="287" cy="132" r="2.5" fill="#2f2f33"/>
    <circle cx="193" cy="160" r="2.5" fill="#2f2f33"/><circle cx="287" cy="160" r="2.5" fill="#d4a23c"/>
  </svg>
  <div class="abs gold" style="left:201px;top:129px;font-size:6px">Lorem ipsum</div>
  <div class="abs" style="left:295px;top:129px;font-size:6px">Lorem ipsum</div>
  <div class="abs" style="left:201px;top:157px;font-size:6px">Lorem ipsum</div>
  <div class="abs gold" style="left:295px;top:157px;font-size:6px">Lorem ipsum</div>
  <p class="body" style="left:201px;top:137px;width:55px;font-size:3.2px">Lorem ipsum dolor sit amet, consectetuer adipiscing elit, sed diam nonummy nibh euismod</p>
  <p class="body" style="left:295px;top:137px;width:55px;font-size:3.2px">Lorem ipsum dolor sit amet, consectetuer adipiscing elit, sed diam nonummy nibh euismod</p>
  <p class="body" style="left:201px;top:165px;width:55px;font-size:3.2px">Lorem ipsum dolor sit amet, consectetuer adipiscing elit, sed diam nonummy nibh euismod</p>
  <p class="body" style="left:295px;top:165px;width:55px;font-size:3.2px">Lorem ipsum dolor sit amet, consectetuer adipiscing elit, sed diam nonummy nibh euismod</p>
  <div class="folio">07</div><div class="folio-line"></div>
</section>

<section class="slide c2 r3">
  <div class="photo" style="inset:0;background:linear-gradient(160deg,#4a4a4d,#2d2d30 55%,#1c1c1e)" role="img" aria-label="Dark construction site with cranes"></div>
  <div class="abs" style="left:117px;top:46px;width:134px;height:118px;border:1.5px solid #fff;background:rgba(30,30,32,.55)"></div>
  <div class="abs" style="left:117px;top:50px;width:134px;text-align:center;font-family:'Oswald',sans-serif;font-weight:600;font-size:30px;line-height:35px;color:#fff">ABOUT<br>OUR<br><span class="gold">PROJECT</span></div>
</section>

<section class="slide c3 r3">
  <div class="brand-mini"><i></i>NIVEL CREST</div>
  <div class="abs" style="left:19px;top:35px;width:140px;height:140px;border:1px solid #999"></div>
  <div class="photo" style="left:25px;top:40px;width:128px;height:130px;background:linear-gradient(200deg,#eaf2fb,#8fb3d6 45%,#3f6a97 75%,#1f3554)" role="img" aria-label="Looking up between glass towers into a blue sky"></div>
  <div class="abs" style="left:169px;top:35px;font-size:10px;font-weight:500">PORTFOLIO OF</div>
  <div class="abs h-bold" style="left:169px;top:47px;font-size:20px">PROJECTS</div>
  <p class="body just" style="left:169px;top:72px;width:187px;font-size:4px">Lorem ipsum dolor sit amet, consectetuer adipiscing elit, sed diam nonummy nibh euismod tincidunt ut laoreet dolore magna aliquam erat volutpat. Ut wisi enim ad minim veniam, quis nostrud exerci tation ullamcorper suscipit lobortis nisl ut aliquip ex ea commodo consequat. Duis autem vel eum iriure dolor in hendrerit in vulputate velit esse</p>
  <p class="body just" style="left:169px;top:106px;width:187px;font-size:4px">Lorem ipsum dolor sit amet, consectetuer adipiscing elit, sed diam nonummy nibh euismod tincidunt ut laoreet dolore magna aliquam erat volutpat. Ut wisi enim ad minim veniam, quis nostrud exerci tation ullamcorper suscipit lobortis nisl ut aliquip ex ea commodo consequat. Duis autem vel eum iriure dolor in hendrerit in vulputate velit esse</p>
  <p class="bullet" style="left:169px;top:141px;width:187px;font-size:3.8px">Lorem ipsum dolor sit amet, consectetuer adipiscing elit, sed diam nonummy nibh euismod tincidunt ut laoreet dolore magna</p>
  <p class="bullet hollow" style="left:169px;top:163px;width:187px;font-size:3.8px">Lorem ipsum dolor sit amet, consectetuer adipiscing elit, sed diam nonummy nibh euismod tincidunt ut laoreet dolore magna</p>
  <div class="folio">09</div><div class="folio-line"></div>
</section>

<section class="slide c1 r4">
  <div class="brand-mini"><i></i>NIVEL CREST</div>
  <div class="abs" style="left:0;top:110px;width:190px;height:100px;background:linear-gradient(45deg,#f0f0f0,#fafafa)"></div>
  <div class="phone" style="left:31px;top:24px"><h6>Lorem ipsum dolor</h6><div class="glyph"></div><p>To introduce the students to the changing landscape of marketing and equip them with knowledge.</p></div>
  <div class="phone" style="left:87px;top:52px"><h6>Dolor sit amet, conse</h6><div class="glyph"></div><p>You will learn concepts and ideas in digital marketing as well as how to use different tools.</p></div>
  <div class="phone" style="left:142px;top:83px"><h6>Consec</h6><div class="glyph" style="border-radius:50%"></div><p>You are required to pass 80% of the evaluation test to obtain the certificate.</p></div>
  <div class="abs" style="left:198px;top:60px;font-size:23px;font-weight:300;letter-spacing:.5px">USE <b class="gold" style="font-weight:700">CASES</b></div>
  <p class="body" style="left:198px;top:91px;width:160px;font-size:4.5px">Lorem ipsum dolor sit amet, consectetuer adipiscing elit, sed diam nonummy nibh euismod tincidunt ut laoreet dolore magna aliquam erat volutpat. Ut wisi enim ad minim veniam, quis nostrud exerci tation ullamcorper suscipit lobortis nisl ut aliquip ex ea commodo consequat. Duis autem vel eum iriure dolor in hendrerit i</p>
  <p class="body" style="left:198px;top:134px;width:160px;font-size:4.5px">Lorem ipsum dolor sit amet, consectetuer adipiscing elit, sed diam nonummy nibh euismod tincidunt ut laoreet dolore magna aliquam erat volutpat. Ut wisi enim ad minim veniam, quis nostrud exerci tation ullamcorper suscipit lobortis nisl ut aliquip ex ea commodo consequat. Duis autem vel eum iriure dolor in hendrerit in</p>
  <div class="folio">10</div><div class="folio-line"></div>
</section>

<section class="slide c2 r4">
  <div class="brand-mini"><i></i>NIVEL CREST</div>
  <div class="abs" style="left:0;width:374px;top:26px;text-align:center;font-size:14px;font-weight:500">LOREM IPSUM <b class="gold" style="font-weight:700">PROJECT</b></div>
  <p class="body" style="left:30px;top:50px;width:314px;text-align:center;font-size:4.3px">Lorem ipsum dolor sit amet, consectetuer adipiscing elit, sed diam nonummy nibh euismod tincidunt ut laoreet dolore magna aliquam erat volutpat. Ut wisi enim ad minim veniam, quis nostrud exerci tation ullamcorper suscipit lobortis nisl utea commodo consequat. Duis autem vel eum iriure dolor in hendrerit i</p>
  <p class="body" style="left:30px;top:74px;width:314px;text-align:center;font-size:4.3px">Lorem ipsum dolor sit amet, consectetuer adipiscing elit, sed diam nonummy nibh m ipsum dolor sit amet, consectetuer adipiscing elit, sed diam nonummy nibh euismod tincidunt ut laoreet dolore magna.</p>
  <div class="photo thumb" style="left:14px;background:linear-gradient(135deg,#1e3c6b,#4f86c6 50%,#d9e3ee)" role="img" aria-label="Hand touching a glowing digital interface"></div>
  <div class="photo thumb" style="left:102px;background:linear-gradient(135deg,#e6e9ee,#9aa3b0 55%,#3b4252)" role="img" aria-label="Business team meeting around a table"></div>
  <div class="photo thumb" style="left:190px;background:linear-gradient(135deg,#0b1e4a,#2f6fd1 55%,#10264f)" role="img" aria-label="Finger pressing a blue holographic button"></div>
  <div class="photo thumb" style="left:278px;background:linear-gradient(135deg,#10323f,#2d7f93 50%,#c9a35a)" role="img" aria-label="Digital network graphic"></div>
  <div class="thumb-cap" style="left:14px"><h5>Lorem ipsum</h5><p>Lorem ipsum dolor sit amet, consectetuer adipiscing elit, sed diam nonummy nibh euismod tincidunt ut laoreet</p></div>
  <div class="thumb-cap" style="left:102px"><h5>Lorem ipsum</h5><p>Lorem ipsum dolor sit amet, consectetuer adipiscing elit, sed diam nonummy nibh euismod tincidunt ut laoreet</p></div>
  <div class="thumb-cap" style="left:190px"><h5>Lorem ipsum</h5><p>Lorem ipsum dolor sit amet, consectetuer adipiscing elit, sed diam nonummy nibh euismod tincidunt ut laoreet</p></div>
  <div class="thumb-cap" style="left:278px"><h5>Lorem ipsum</h5><p>Lorem ipsum dolor sit amet, consectetuer adipiscing elit, sed diam nonummy nibh euismod tincidunt ut laoreet</p></div>
  <div class="folio">11</div><div class="folio-line"></div>
</section>

<section class="slide c3 r4">
  <div class="brand-mini"><i></i>NIVEL CREST</div>
  <div class="abs gold" style="left:11px;top:5px;font-size:17px;font-weight:700">Price Lists</div>
  <div class="price" style="left:64px">
    <div class="card" style="background:linear-gradient(#6e6e72,#b4b4b8)"></div>
    <div class="stars"><i style="background:#444">★</i></div>
    <div class="tab" style="background:#3b3b3f;top:14px">STANDART</div>
    <div class="strip">Lorem ipsum dolor sit amet, consectetuer</div>
    <ul><li>Lorem ipsum dolor</li><li>Lorem ipsum dolor</li><li>Lorem ipsum dolor</li><li>Lorem ipsum dolor</li><li>Lorem ipsum dolor</li><li>Lorem ipsum dolor</li></ul>
    <div class="buy">BUY NOW</div>
    <div class="badge">14<sup>99</sup></div>
    <div class="note">Lorem ipsum dolor sit amet, consectetuer adipiscing.</div>
  </div>
  <div class="price" style="left:148px">
    <div class="card" style="background:linear-gradient(#2a2a2d,#555559)"></div>
    <div class="stars"><i style="background:#333">★</i><i style="background:#333">★</i></div>
    <div class="tab" style="background:#1e1e20;top:14px">BUSINESS</div>
    <div class="strip">Lorem ipsum dolor sit amet, consectetuer</div>
    <ul><li>Lorem ipsum dolor</li><li>Lorem ipsum dolor</li><li>Lorem ipsum dolor</li><li>Lorem ipsum dolor</li><li>Lorem ipsum dolor</li><li>Lorem ipsum dolor</li></ul>
    <div class="buy">BUY NOW</div>
    <div class="badge" style="border-color:#222">34<sup>99</sup></div>
    <div class="note">Lorem ipsum dolor sit amet, consectetuer adipiscing.</div>
  </div>
  <div class="price" style="left:232px">
    <div class="card" style="background:linear-gradient(#c08a2c,#e3b556)"></div>
    <div class="stars"><i style="background:var(--gold)">★</i><i style="background:var(--gold)">★</i><i style="background:var(--gold)">★</i></div>
    <div class="tab" style="background:var(--gold-dark);top:14px">PREMIUM</div>
    <div class="strip">Lorem ipsum dolor sit amet, consectetuer</div>
    <ul><li>Lorem ipsum dolor</li><li>Lorem ipsum dolor</li><li>Lorem ipsum dolor</li><li>Lorem ipsum dolor</li><li>Lorem ipsum dolor</li><li>Lorem ipsum dolor</li></ul>
    <div class="buy">BUY NOW</div>
    <div class="badge" style="border-color:var(--gold)">54<sup>99</sup></div>
    <div class="note">Lorem ipsum dolor sit amet, consectetuer adipiscing.</div>
  </div>
  <div class="folio">12</div><div class="folio-line"></div>
</section>

<section class="slide c1 r5">
  <div class="brand-mini"><i></i>NIVEL CREST</div>
  <div class="abs" style="left:17px;top:94px;font-size:11.5px;font-weight:500">TIMELINE OF</div>
  <div class="abs h-bold" style="left:17px;top:106px;font-size:18px">ROADMAP</div>
  <div class="abs" style="left:18px;top:126px;font-size:9px;font-weight:500">FOR 2 YEARS</div>
  <div class="abs" style="left:17px;top:145px;width:21px;height:21px;border-radius:50%;background:var(--panel);color:#fff;font-weight:800;font-size:12px;text-align:center;line-height:21px">A</div>
  <div class="abs gold" style="left:43px;top:144px;font-size:10px;font-weight:500">2019</div>
  <p class="body" style="left:43px;top:157px;width:45px;font-size:2.8px">Lorem ipsum dolor sit amet, consectetuer adipiscing elit, sed diam</p>
  <div class="abs" style="left:101px;top:145px;width:21px;height:21px;border-radius:50%;background:var(--panel);color:#fff;font-weight:800;font-size:12px;text-align:center;line-height:21px">B</div>
  <div class="abs gold" style="left:126px;top:144px;font-size:10px;font-weight:500">2020</div>
  <p class="body" style="left:126px;top:157px;width:45px;font-size:2.8px">Lorem ipsum dolor sit amet, consectetuer adipiscing elit, sed diam</p>
  <svg class="abs" style="left:0;top:0" width="374" height="210" viewBox="0 0 374 210" font-family="Montserrat, sans-serif" font-weight="600" text-anchor="middle">
    <path d="M332 171 C260 172 210 168 200 150 C196 140 200 128 200 117 M200 85 C230 82 257 75 258 66 M258 58 C250 46 190 38 181 46 M181 46 C175 58 155 58 152 60 M152 52 C140 40 130 44 127 42" fill="none" stroke="#d4a23c" stroke-width="1.1"/>
    <path d="M331 128 V170 M200 103 V118 M258 66 V78 M152 64 V70 M181 48 V54" stroke="#2f2f33" stroke-width=".9" stroke-dasharray="1.5 1.5"/>
    <circle cx="332" cy="171" r="2.2" fill="#2f2f33"/>
    <path d="M331 130 l-6 -10 a24 24 0 1 1 12 0z" fill="#3b3b3f"/><circle cx="331" cy="97" r="19" fill="#fff"/><text x="331" y="106" font-size="26" fill="#d4a23c" font-weight="700">1</text>
    <path d="M200 104 l-4 -6 a16 16 0 1 1 8 0z" fill="#3b3b3f"/><circle cx="200" cy="82.5" r="12.5" fill="#fff"/><text x="200" y="88" font-size="15" fill="#d4a23c">2</text>
    <path d="M258 78 l-3 -4 a11 11 0 1 1 6 0z" fill="#3b3b3f"/><circle cx="258" cy="63.5" r="8.5" fill="#fff"/><text x="258" y="67.5" font-size="11" fill="#d4a23c">3</text>
    <path d="M152 70 l-2 -3 a7.5 7.5 0 1 1 4 0z" fill="#3b3b3f"/><circle cx="152" cy="60" r="5.8" fill="#fff"/><text x="152" y="63" font-size="7.5" fill="#d4a23c">4</text>
    <path d="M181 54 l-1.5 -2.5 a6 6 0 1 1 3 0z" fill="#3b3b3f"/><circle cx="181" cy="46" r="4.5" fill="#fff"/><text x="181" y="48.5" font-size="6" fill="#d4a23c">5</text>
    <path d="M127 47 l-1 -2 a4.5 4.5 0 1 1 2 0z" fill="#3b3b3f"/><circle cx="127" cy="41" r="3.3" fill="#fff"/><text x="127" y="43" font-size="4.5" fill="#d4a23c">6</text>
  </svg>
  <div class="pin-label" style="left:74px;top:38px"><h6>Lorem Ipsum</h6><p>Lorem ipsum dolor sit amet, consectetuer adipiscing elit, sed diam nonummy nibh euismod tincid</p></div>
  <div class="pin-label" style="left:193px;top:32px"><h6>Lorem Ipsum</h6><p>Lorem ipsum dolor sit amet, consectetuer adipiscing elit, sed diam nonummy nibh euismod tincid</p></div>
  <div class="pin-label" style="left:277px;top:35px"><h6>Lorem Ipsum</h6><p>Lorem ipsum dolor sit amet, consectetuer adipiscing elit, sed diam nonummy nibh euismod tincid</p></div>
  <div class="pin-label" style="left:139px;top:87px"><h6>Lorem Ipsum</h6><p>Lorem ipsum dolor sit amet, consectetuer adipiscing elit, sed diam nonummy nibh euismod tincid</p></div>
  <div class="pin-label" style="left:263px;top:113px"><h6>Lorem Ipsum</h6><p>Lorem ipsum dolor sit amet, consectetuer adipiscing elit, sed diam nonummy nibh euismod tincid</p></div>
  <div class="folio">13</div><div class="folio-line"></div>
</section>

<section class="slide c2 r5">
  <div class="brand-mini"><i></i>NIVEL CREST</div>
  <div class="abs" style="left:0;width:374px;top:26px;text-align:center;font-size:13px;font-weight:700;letter-spacing:.5px">ORGANIZATIONAL CHART</div>
  <p class="body" style="left:30px;top:45px;width:314px;text-align:center;font-size:4.3px">Lorem ipsum dolor sit amet, consectetuer adipiscing elit, sed diam nonummy nibh euismod tincidunt ut laoreet dolore magna aliquam erat volutpat. Ut wisi enim ad minim veniam, quis nostrud exerci tation ullamcorper suscipit lobortis nisl ut aliquip ex ea commodo consequat. Duis autem</p>
  <p class="body" style="left:30px;top:68px;width:314px;text-align:center;font-size:4.3px">Lorem ipsum dolor sit amet, cons ectetuer adipiscing elit, sed diam nonummy nibh euismod tincidunt ut laoreet dolore magna aliquam erat volutpat.</p>
  <div class="abs team-band"></div>
  <div class="member" style="left:13px"><div class="avatar" role="img" aria-label="Portrait of Alan Reed"></div><h5>ALAN REED</h5><p>Ipsum dolor sit amet, cons ectetuer adipiscing elit, sed diam nonummy nibh euismod tincidunt ut laoreet dolore magna aliquam erat volutpat.</p></div>
  <div class="member" style="left:103px"><div class="avatar" role="img" aria-label="Portrait of Clara Voss"></div><h5>CLARA VOSS</h5><p>Ipsum dolor sit amet, cons ectetuer adipiscing elit, sed diam nonummy nibh euismod tincidunt ut laoreet dolore magna aliquam erat volutpat.</p></div>
  <div class="member" style="left:190px"><div class="avatar" role="img" aria-label="Portrait of Alan Reed"></div><h5>ALAN REED</h5><p>Ipsum dolor sit amet, cons ectetuer adipiscing elit, sed diam nonummy nibh euismod tincidunt ut laoreet dolore magna aliquam erat volutpat.</p></div>
  <div class="member" style="left:280px"><div class="avatar" role="img" aria-label="Portrait of Clara Voss"></div><h5>CLARA VOSS</h5><p>Ipsum dolor sit amet, cons ectetuer adipiscing elit, sed diam nonummy nibh euismod tincidunt ut laoreet dolore magna aliquam erat volutpat.</p></div>
  <div class="folio">13</div><div class="folio-line"></div>
</section>

<section class="slide c3 r5" style="background:linear-gradient(90deg,#ffffff 30%,#e9e9ea 100%)">
  <div class="photo" style="left:200px;top:0;width:174px;height:210px;background:linear-gradient(180deg,#f2f2f3,#cfcfd1 55%,#8c8c8f 80%,#e6e6e7)" role="img" aria-label="Building under construction with crane in fog"></div>
  <div class="abs gold" style="left:12px;top:52px;font-size:12px;font-weight:800;letter-spacing:1px">NIVEL CREST</div>
  <div class="abs gold" style="left:14px;top:67px;font-size:5px;font-weight:700;letter-spacing:1.6px">BUILD SMARTER</div>
  <div class="abs" style="left:12px;top:116px;font-size:13px;font-weight:500">Contact <b class="gold" style="font-weight:700">US</b></div>
  <ul class="abs" style="left:12px;top:135px;list-style:none;font-size:7.2px;color:#555;line-height:11.5px">
    <li><span class="gold">●</span> 555-014-2290</li>
    <li><span class="gold">●</span> info@nivelcrest.com</li>
    <li><span class="gold">●</span> Your address, your city, box 88900</li>
  </ul>
  <div class="abs" style="left:12px;top:183px;font-size:8px;letter-spacing:1.8px;color:#444">www.<span class="gold">nivelcrest</span>.com</div>
</section>

</body>
</html>
```